Business Card for premium dental clinic

We are a premium dental clinic based in Brasov, Romania with more than 15 year on the market, providing quality dental treatment made by a team of more specialized dentists, working with modern equipment as a solution to beautiful and healthy teeth.

Our current logo for the clinic use 2 square with colors black and gold - dr Ternisu - studio, using family fonts Bodoni, Myriad Pro and Segoe Print.
Depending on the printing we used some gold CMYK background or gold foil picture background or a gold gradient.
We want a business card:
- eye catching business card
- distinguished business card
- premium design
- to keep the color scheme of black and gold
- to attract the customers to spent time reading the information
- modern concept

```html
<!DOCTYPE html>
<html lang="en">
<head>
<meta charset="utf-8">
<title>Dr Ternisu Studio – Business Card</title>
<link rel="stylesheet" href="https://fonts.googleapis.com/css2?family=Montserrat:wght@400;500;600&display=swap">
<style>
  :root {
    --bg: #3b3b3c;
    --card-dark: #2b2e30;
    --paper: #f7f7f5;
    --gold: #c9a12a;
    --brown-black: #1c120f;
    --ink: #4a4a4a;
    --white: #ffffff;
  }
  * { box-sizing: border-box; margin: 0; padding: 0; }
  html, body {
    width: 1200px; height: 866px; overflow: hidden;
    background: var(--bg);
    font-family: "Montserrat", Arial, sans-serif;
  }
  .canvas { position: relative; width: 1200px; height: 866px; }

  .card {
    position: absolute;
    width: 600px; height: 342px;
    border-radius: 3px;
    overflow: hidden;
    box-shadow: 0 12px 30px rgba(0,0,0,.45);
  }

  /* Back side */
  .card-back { left: 70px; top: 60px; background: var(--card-dark); }
  .card-back .brand {
    position: absolute; left: 50%; top: 128px; transform: translateX(-50%);
    display: flex; align-items: center; gap: 14px;
    color: var(--gold); font-weight: 600; font-size: 34px; letter-spacing: .5px;
    white-space: nowrap;
  }
  .card-back .web {
    position: absolute; left: 0; right: 0; top: 262px; text-align: center;
    color: var(--white); font-size: 15px; font-weight: 500; letter-spacing: 3px;
  }

  /* Front side */
  .card-front { left: 530px; top: 464px; background: var(--paper); }
  .card-front .wave { position: absolute; inset: 0; width: 100%; height: 100%; }
  .brand-square { width: 26px; height: 26px; background: var(--gold); flex: none; }
  .card-front .brand {
    position: absolute; left: 36px; top: 146px;
    display: flex; align-items: center; gap: 10px;
    color: var(--brown-black); font-weight: 600; font-size: 21px; white-space: nowrap;
  }
  .card-front .divider {
    position: absolute; left: 276px; top: 72px; width: 2px; height: 118px;
    background: var(--gold);
  }
  .contact { position: absolute; left: 298px; top: 66px; }
  .contact .name {
    color: var(--gold); font-weight: 600; font-size: 19px; letter-spacing: 1px;
  }
  .contact .role { color: var(--ink); font-size: 14px; margin: 2px 0 12px; }
  .contact ul { list-style: none; }
  .contact li {
    display: flex; align-items: center; gap: 10px;
    color: var(--ink); font-size: 13px; line-height: 24px;
  }
  .contact svg { width: 14px; height: 14px; flex: none; }
  .address {
    position: absolute; right: 26px; bottom: 26px; text-align: right;
    color: var(--white); font-size: 13px; line-height: 20px;
  }
</style>
</head>
<body>
<main class="canvas">

  <section class="card card-back" aria-label="Business card back">
    <div class="brand"><span class="brand-square"></span>dr Ternisu Studio</div>
    <p class="web">www.drternisu.ro</p>
  </section>

  <section class="card card-front" aria-label="Business card front">
    <svg class="wave" viewBox="0 0 600 342" preserveAspectRatio="none" aria-hidden="true">
      <path d="M0,254 C300,266 520,224 600,96 L600,342 L0,342 Z" fill="var(--gold)"/>
      <path d="M0,276 C310,286 535,246 600,128 L600,342 L0,342 Z" fill="var(--brown-black)"/>
    </svg>

    <div class="brand"><span class="brand-square"></span>dr Ternisu Studio</div>
    <div class="divider"></div>

    <div class="contact">
      <p class="name">MARA ILESCU</p>
      <p class="role">Doctor</p>
      <ul>
        <li>
          <svg viewBox="0 0 24 24"><path fill="var(--gold)" d="M6.6 10.8a15.1 15.1 0 0 0 6.6 6.6l2.2-2.2a1 1 0 0 1 1-.25 11.4 11.4 0 0 0 3.6.57 1 1 0 0 1 1 1V20a1 1 0 0 1-1 1A17 17 0 0 1 3 4a1 1 0 0 1 1-1h3.5a1 1 0 0 1 1 1c0 1.25.2 2.450.57 3.57a1 1 0 0 1-.25 1z"/></svg>
          +40 268 555 019
        </li>
        <li>
          <svg viewBox="0 0 24 24"><rect x="2" y="5" width="20" height="14" rx="1" fill="var(--gold)"/><path d="M2.5 6l9.5 7 9.5-7" stroke="var(--paper)" stroke-width="1.6" fill="none"/></svg>
          m.ilescu@drternisu.ro
        </li>
        <li>
          <svg viewBox="0 0 24 24"><g fill="none" stroke="var(--gold)" stroke-width="2"><circle cx="12" cy="12" r="9"/><ellipse cx="12" cy="12" rx="4" ry="9"/><path d="M3 12h18M5 7h14M5 17h14"/></g></svg>
          www.drternisu.ro
        </li>
      </ul>
    </div>

    <p class="address">Strada Lungă nr 24,<br>500035 Brașov</p>
  </section>

</main>
</body>
</html>
```